Brightmill Data Works

Our company is about IT hardwares and IT solutions. IT hardware such as PC, RAMS, storage and servers. IT solutions such as project management, BA. We are also selling new technology too.

Target Market(s)

Consumer, Small to Medium Business, Corporate

Requirements
Must have
• The business card must have the following:
• Name:
• Title:
• Contact Number:
• Email address:
• Website:
• Color: Must match the logo color upgrade

```html
<!DOCTYPE html>
<html lang="en">
<head>
<meta charset="utf-8">
<title>Brightmill Data Works – Business Card</title>
<link rel="stylesheet" href="https://fonts.googleapis.com/css2?family=Open+Sans:wght@400;600&family=Rajdhani:wght@700&display=swap">
<style>
  :root {
    --backdrop: #656565;
    --card-white: #f6f6f6;
    --card-dark: #4a4a4a;
    --card-edge: #5c5c5c;
    --pattern-tone: #555555;
    --ink: #3f3f3f;
    --ink-soft: #2f2f2f;
    --amber: #d9822b;
    --divider: #c9c9c9;
  }
  * { margin: 0; padding: 0; box-sizing: border-box; }
  html, body { width: 1200px; height: 802px; overflow: hidden; }
  body {
    background: var(--backdrop);
    position: relative;
    font-family: "Open Sans", Arial, sans-serif;
  }
  .card {
    position: absolute;
    top: 274px;
    width: 443px;
    height: 265px;
    box-shadow: 0 12px 14px rgba(0,0,0,0.28);
  }
  .card::after {
    content: "";
    position: absolute;
    left: 0; right: 0; bottom: -11px;
    height: 11px;
    background: var(--card-edge);
  }
  .card-front { left: 136px; background: var(--card-white); }
  .card-back { left: 625px; background: var(--card-dark); }

  .brand {
    position: absolute;
    left: 20px;
    width: 210px;
    top: 82px;
    text-align: center;
  }
  .brand-dot {
    display: block;
    width: 34px; height: 34px;
    margin: 0 auto 12px;
    border-radius: 50%;
    background: var(--amber);
  }
  .brand-name {
    font-family: "Rajdhani", "Arial Narrow", sans-serif;
    font-weight: 700;
    font-size: 25px;
    line-height: 1.05;
    color: var(--ink);
    letter-spacing: 0.5px;
    text-transform: uppercase;
  }
  .divider {
    position: absolute;
    left: 236px; top: 79px;
    width: 1px; height: 106px;
    background: var(--divider);
  }
  .contact-block { position: absolute; left: 255px; top: 83px; }
  .person-name {
    font-size: 16px;
    color: var(--amber);
    text-transform: uppercase;
    line-height: 1.1;
  }
  .person-title {
    font-size: 13px;
    color: var(--ink-soft);
    margin: 1px 0 0 2px;
  }
  .contact-list { list-style: none; margin-top: 19px; }
  .contact-list li {
    font-size: 13px;
    color: var(--ink-soft);
    line-height: 16px;
    display: flex;
    align-items: center;
    gap: 5px;
  }
  .contact-list svg { width: 9px; height: 9px; fill: var(--amber); flex: none; }

  .back-pattern {
    position: absolute; inset: 0;
    background: linear-gradient(135deg, var(--pattern-tone), var(--card-dark) 60%, var(--pattern-tone));
  }
  .back-brand {
    position: absolute;
    left: 262px; top: 136px;
    display: flex; align-items: center; gap: 8px;
  }
  .back-brand .brand-dot { width: 20px; height: 20px; margin: 0; }
  .back-brand .brand-name { color: var(--amber); font-size: 19px; }
</style>
</head>
<body>
  <section class="card card-front">
    <div class="brand">
      <span class="brand-dot"></span>
      <p class="brand-name">Brightmill<br>Data Works</p>
    </div>
    <div class="divider"></div>
    <div class="contact-block">
      <h1 class="person-name">Daniel Harper</h1>
      <p class="person-title">Managing Director</p>
      <ul class="contact-list">
        <li><svg viewBox="0 0 10 10"><path d="M1 4 Q5 0 9 4 L8 5 L6.5 4 L6.5 3.2 Q5 2.6 3.5 3.2 L3.5 4 L2 5 Z M2.5 5.5 H7.5 L8.5 9 H1.5 Z"/></svg>044-987 650 312</li>
        <li><svg viewBox="0 0 10 10"><path d="M0.5 2 H9.5 V8 H0.5 Z" /><path d="M0.5 2 L5 5.5 L9.5 2" fill="none" stroke="#f6f6f6" stroke-width="0.9"/></svg>hello@brightmill.com</li>
        <li><svg viewBox="0 0 10 10"><circle cx="5" cy="5" r="4.5"/></svg>www.brightmilldata.com</li>
      </ul>
    </div>
  </section>

  <section class="card card-back">
    <div class="back-pattern" role="img" aria-label="Repeating faint brand pattern in grey tones"></div>
    <div class="back-brand">
      <span class="brand-dot"></span>
      <p class="brand-name">Brightmill Data Works</p>
    </div>
  </section>
</body>
</html>
```